Verodex business card

Business card for sustainable investment company called "Verodex". Verodex is an exchange platform selling carbon credits between buyers and sellers. Carbon Credits are an environmental commodity for reducing global carbon emissions.

the card should obviously have our logo and the theme should be sustainability/environment mixed with a trading platform.

Contact Information for Business Card

Logo, Name, Title, Phone, Email

Colors
0054AA
0677BA
7BADD7
CADEEF
E8F1F8
0094D4
00A9DD
6FCCEA
C7EBF8
E9F6FB
00AB8E
00BBA5
67D7C9
C6EFE9
E9F9F6
59FF00
82FF00
B8FF75
E3FFCB
F4FFEA

```html
<!DOCTYPE html>
<html lang="en">
<head>
<meta charset="utf-8">
<title>Verodex business card</title>
<link href="https://fonts.googleapis.com/css2?family=Open+Sans:wght@400;600;700&display=swap" rel="stylesheet">
<style>
  :root {
    --page-bg: #e4e7ec;
    --card-paper: #fdfdf4;
    --navy: #0f2a50;
    --brand-blue: #3f87c9;
    --sky: #4cb3dc;
    --ink: #1c1c1c;
    --rule: #2b2f3a;
  }
  * { margin: 0; padding: 0; box-sizing: border-box; }
  html, body {
    width: 1200px; height: 780px; overflow: hidden;
    background: var(--page-bg);
    font-family: "Open Sans", Arial, sans-serif;
  }
  .canvas {
    width: 1200px; height: 780px;
    display: flex; align-items: center; justify-content: center; gap: 48px;
  }
  .card {
    width: 530px; height: 304px;
    background: var(--card-paper);
    position: relative;
    box-shadow: 0 10px 28px rgba(20, 30, 50, .22);
    overflow: hidden;
  }
  /* contact side */
  .brand-block {
    position: absolute; left: 28px; top: 0; bottom: 0; width: 180px;
    display: flex; align-items: center; gap: 12px;
  }
  .brand-dot {
    width: 22px; height: 22px; border-radius: 50%;
    background: var(--brand-blue);
    flex: none;
  }
  .brand-name {
    font-weight: 700; font-size: 30px; color: var(--brand-blue);
    letter-spacing: .5px;
  }
  .divider { position: absolute; left: 0; top: 0; }
  .details {
    position: absolute; left: 282px; top: 62px; right: 14px;
    color: var(--ink);
  }
  .person-name {
    font-weight: 700; font-size: 27px; color: var(--sky); line-height: 1.1;
    white-space: nowrap;
  }
  .person-title {
    font-weight: 600; font-size: 15px; margin-top: 4px;
  }
  .address { font-size: 14px; line-height: 1.35; margin-top: 8px; }
  .contact-list { list-style: none; margin-top: 8px; font-size: 14px; line-height: 1.45; }
  .contact-list li { display: flex; align-items: center; gap: 7px; white-space: nowrap; }
  .contact-list svg { width: 12px; height: 12px; flex: none; }
  /* wordmark side */
  .wordmark {
    position: absolute; inset: 0;
    display: flex; align-items: center; justify-content: center; gap: 18px;
  }
  .wordmark-square {
    width: 34px; height: 34px; background: var(--brand-blue);
  }
  .wordmark-name {
    font-weight: 700; font-size: 58px; color: var(--navy); letter-spacing: 2px;
  }
</style>
</head>
<body>
<main class="canvas">
  <section class="card card-contact">
    <div class="brand-block">
      <span class="brand-dot"></span>
      <span class="brand-name">Verodex</span>
    </div>
    <svg class="divider" width="530" height="304" aria-hidden="true">
      <line x1="262" y1="40" x2="200" y2="270" stroke="var(--rule)" stroke-width="1"/>
    </svg>
    <div class="details">
      <h1 class="person-name">Marta Velenko</h1>
      <p class="person-title">Managing Director</p>
      <p class="address">1840 Linden Ave. Suite 310<br>Dayton, OH 45402</p>
      <ul class="contact-list">
        <li>
          <svg viewBox="0 0 12 12" aria-hidden="true"><path d="M3 1 L5 3.5 L4 5 Q5 7 7 8 L8.5 7 L11 9 L9.5 11 Q4 10.5 1 2.5 Z" fill="var(--brand-blue)"/></svg>
          (555) 204-6173
        </li>
        <li>
          <svg viewBox="0 0 12 12" aria-hidden="true"><rect x="1" y="2.5" width="10" height="7" fill="var(--brand-blue)"/><path d="M1 2.5 L6 6.5 L11 2.5" stroke="#fff" fill="none" stroke-width="1"/></svg>
          hello@verodex.example
        </li>
        <li>
          <svg viewBox="0 0 12 12" aria-hidden="true"><circle cx="6" cy="6" r="5" fill="var(--brand-blue)"/><path d="M1 6 H11 M6 1 Q3 6 6 11 M6 1 Q9 6 6 11" stroke="#fff" fill="none" stroke-width=".8"/></svg>
          www.verodex.example
        </li>
      </ul>
    </div>
  </section>

  <section class="card card-front">
    <div class="wordmark">
      <span class="wordmark-square"></span>
      <span class="wordmark-name">VERODEX</span>
    </div>
  </section>
</main>
</body>
</html>
```